Bram Keystone Homes needs a business card

We need a business card for a new company in Canada, Ontario. Our company is all about luxury contraction homes for our clients. Our product and services are custom projects design. Under the business logo that will be created, we want a slogan that will be a memorable phrase for consumers to remember us to tell their friends and relatives.

Additional infomation
- Ludovic Entrasse
- President / Ceo
-519.604.3087

Find point what luxury construction products and services can be done

We like to see colors:
- #663300
- and something other colors or color that would attract the client needs and wants

The final design should communicate leads from new or old clients that will grow our empire. Most of all, we try to work among the budget that clients want

NOTE
- we also need an icon for the business (Example: Instagram, Facebook, and Whatsapp icons)
- We want the company name to be remembered easily for clients and our distributors who would get our orders.
- we need an icon on the business cards: Facebook and Instagram.

Thanks,
Bram Keystone Homes

```html
<!DOCTYPE html>
<html lang="en">
<head>
<meta charset="utf-8">
<title>Bram Keystone Homes – Business Card</title>
<link href="https://fonts.googleapis.com/css2?family=Arimo:wght@400;700&display=swap" rel="stylesheet">
<style>
  :root {
    --brown: #663300;
    --white: #ffffff;
    --backdrop: #e4e4e6;
    --rule-grey: #a9a9a9;
    --social-blue: #3b5e9e;
  }
  * { box-sizing: border-box; margin: 0; padding: 0; }
  html, body {
    width: 1200px;
    height: 900px;
    overflow: hidden;
    background: var(--backdrop);
    font-family: "Arimo", Arial, sans-serif;
  }
  .stage {
    width: 1200px;
    height: 900px;
    display: flex;
    align-items: center;
    justify-content: center;
    gap: 48px;
  }
  .card {
    width: 530px;
    height: 303px;
    border-radius: 26px;
    display: flex;
    flex-direction: column;
    align-items: center;
    justify-content: center;
    text-align: center;
    box-shadow: 0 6px 18px rgba(0,0,0,0.12);
  }
  .card--front { background: var(--white); color: var(--brown); }
  .card--back  { background: var(--brown); color: var(--white); }

  .wordmark {
    font-weight: 700;
    font-size: 34px;
    letter-spacing: 0.5px;
    line-height: 1;
  }
  .tagline {
    font-size: 12.5px;
    letter-spacing: 0.6px;
    margin-top: 6px;
  }
  .social-row {
    display: flex;
    align-items: center;
    width: 380px;
    margin-top: 30px;
  }
  .social-row .rule {
    flex: 1;
    height: 1px;
    background: var(--rule-grey);
  }
  .social-icons { display: flex; gap: 6px; padding: 0 8px; }
  .social-dot {
    width: 22px;
    height: 22px;
    border-radius: 50%;
    background: var(--social-blue);
  }
  .person-name {
    font-weight: 700;
    font-size: 24px;
    letter-spacing: 0.5px;
    margin-top: 24px;
  }
  .person-title {
    font-size: 19px;
    margin-top: 2px;
  }
  .contact-rule {
    width: 170px;
    height: 1px;
    background: var(--white);
    margin: 10px 0 10px;
  }
  .phone {
    font-size: 21px;
    letter-spacing: 1px;
  }
</style>
</head>
<body>
  <main class="stage">
    <section class="card card--front" aria-label="Card front">
      <div class="wordmark">Bram Keystone Homes</div>
      <div class="tagline">- HOME RENOVATIONS - CUSTOM PROJECT DESIGN -</div>
      <div class="social-row">
        <span class="rule"></span>
        <span class="social-icons">
          <span class="social-dot" aria-label="Social profile"></span>
          <span class="social-dot" aria-label="Social profile"></span>
        </span>
        <span class="rule"></span>
      </div>
    </section>

    <section class="card card--back" aria-label="Card back">
      <div class="wordmark">Bram Keystone Homes</div>
      <div class="tagline">- HOME RENOVATIONS - CUSTOM PROJECT DESIGN -</div>
      <div class="person-name">LUDOVIC ENTRASSE</div>
      <div class="person-title">President / CEO</div>
      <div class="contact-rule"></div>
      <div class="phone">519.604.3087</div>
    </section>
  </main>
</body>
</html>
```